Civic Viewing Studio SmartPhone

We are looking for a fresh new look for our famous Screen Sense Pocketdeck cards. These cards are used as a pedagogical device by teachers and students to help people critically analyze media messages.

Now that we are in the era of Zolara 7, we would like the Screen Sense Pocketdeck to look fresh and new. All the content stays the same, but graphic elements, color and overall design can be changed to look contemporary and modern.

Target Market(s)

Teenagers, young adults, secondary and college teachers

Industry/Entity Type

Education

Colors

Designer to choose colors to be used in the design.

Requirements
Must have
• All the content that is on the current card, with icons and text
Nice to have
• Fresh use of color
• More modern phone design like the smartphones people use today
Should not have
• ...too much black

```html
<!DOCTYPE html>
<html lang="en">
<head>
<meta charset="utf-8">
<title>Civic Viewing Studio – Screen Sense Pocketdeck</title>
<link rel="stylesheet" href="https://fonts.googleapis.com/css2?family=Quicksand:wght@500;700&display=swap">
<style>
  :root{
    --bg:#efefef;
    --ink:#1f1f24;
    --muted:#8a8a90;
    --white:#ffffff;
    --pink:#ff8fc0;
    --blue:#8fb3e6;
    --peach:#ffb8a0;
    --teal:#17b8c8;
    --green:#4cb84c;
    --yellow:#f5c91a;
    --orange:#f47a26;
    --card:rgba(255,255,255,.72);
    --tile:rgba(255,255,255,.85);
    --icon-grey:#4a4a50;
  }
  *{box-sizing:border-box;margin:0;padding:0}
  html,body{width:1200px;height:1199px;overflow:hidden}
  body{background:var(--bg);font-family:"Quicksand",sans-serif;color:var(--ink);position:relative}

  .screen{
    position:absolute;width:352px;height:754px;border-radius:42px;overflow:hidden;
    background:
      radial-gradient(circle at 10% 18%, var(--pink) 0, rgba(255,143,192,0) 55%),
      radial-gradient(circle at 95% 30%, var(--blue) 0, rgba(143,179,230,0) 60%),
      radial-gradient(circle at 80% 85%, var(--peach) 0, rgba(255,184,160,0) 55%),
      radial-gradient(circle at 15% 80%, #cfe0f5 0, rgba(207,224,245,0) 55%),
      linear-gradient(160deg,#f7a6cf,#c9d6f0 55%,#f6d3cf);
  }
  .screen--questions{left:175px;top:211px}
  .screen--discuss{left:711px;top:213px}

  .status{position:absolute;top:12px;left:0;right:0;height:20px;color:var(--white);font-size:13px;font-weight:500}
  .status__time{position:absolute;left:32px}
  .status__icons{position:absolute;right:26px;top:3px}

  .screen__title{position:absolute;left:0;right:0;text-align:center;color:var(--white);font-weight:500;letter-spacing:2px;line-height:1.2}
  .screen--questions .screen__title{top:48px;font-size:26px}
  .screen--discuss .screen__title{top:38px;font-size:26px}

  .question{position:absolute;left:10px;width:332px;height:84px;border-radius:12px;background:var(--card);padding:10px 12px}
  .question__head{display:flex;align-items:center;font-size:11px;font-weight:700;letter-spacing:.3px}
  .question__num{width:17px;height:17px;border-radius:3px;color:var(--white);font-size:11px;display:flex;align-items:center;justify-content:center;margin-right:8px}
  .question__time{margin-left:auto;font-size:11px}
  .question__text{margin-top:9px;font-size:14px;font-weight:700;line-height:1.3;letter-spacing:.2px}

  .pager{position:absolute;left:0;right:0;display:flex;justify-content:center;gap:6px}
  .pager i{width:5px;height:5px;border-radius:50%;background:rgba(255,255,255,.5)}
  .pager i.on{background:var(--white)}

  .dock{position:absolute;left:10px;right:10px;height:86px;border-radius:20px;background:var(--card);text-align:center}
  .brand{font-weight:700;font-size:22px;color:#2aa7b8;letter-spacing:.2px}
  .brand--small{font-size:16px}
  .dock__url{font-size:12px;color:var(--muted);margin-top:4px}
  .brand-mark{display:inline-block;width:12px;height:12px;background:#2aa7b8;margin-right:6px;vertical-align:middle}

  .app{position:absolute;width:80px;text-align:center;font-size:10.5px;line-height:1.15;color:var(--ink)}
  .app__tile{width:55px;height:55px;border-radius:12px;margin:0 auto 5px;display:flex;align-items:center;justify-content:center}
  .app__tile svg{width:34px;height:34px;fill:none;stroke:var(--white);stroke-width:2;stroke-linecap:round;stroke-linejoin:round}
  .app__tile--plain{background:var(--tile)}
  .app__tile--plain svg{stroke:var(--icon-grey);stroke-width:1.6}
  .t-teal{background:var(--teal)} .t-green{background:var(--green)}
  .t-yellow{background:var(--yellow)} .t-orange{background:var(--orange)}
</style>
</head>
<body>

<section class="screen screen--questions">
  <div class="status"><span class="status__time">11:53</span>
    <svg class="status__icons" width="44" height="10" viewBox="0 0 44 10"><g fill="#fff"><rect x="0" y="6" width="2" height="4"/><rect x="3" y="4" width="2" height="6"/><rect x="6" y="2" width="2" height="8"/><rect x="9" y="0" width="2" height="10"/><rect x="26" y="1" width="16" height="8" rx="2"/></g></svg>
  </div>
  <h1 class="screen__title">KEY QUESTIONS OF<br>MEDIA LITERACY</h1>

  <article class="question" style="top:144px">
    <div class="question__head"><span class="question__num t-teal">1</span>QUESTION<span class="question__time">5m ago</span></div>
    <p class="question__text">Who is the author and what<br>is the purpose?</p>
  </article>
  <article class="question" style="top:236px">
    <div class="question__head"><span class="question__num t-green">2</span>QUESTION<span class="question__time">4m ago</span></div>
    <p class="question__text">What techniques are used to attract<br>and hold your attention?</p>
  </article>
  <article class="question" style="top:328px">
    <div class="question__head"><span class="question__num t-yellow">3</span>QUESTION<span class="question__time">3m ago</span></div>
    <p class="question__text">What lifestyles, values and points<br>of view are represented?</p>
  </article>
  <article class="question" style="top:420px">
    <div class="question__head"><span class="question__num t-orange">4</span>QUESTION<span class="question__time">2m ago</span></div>
    <p class="question__text">How might different people<br>interpret the message?</p>
  </article>
  <article class="question" style="top:512px">
    <div class="question__head"><span class="question__num t-teal">5</span>QUESTION<span class="question__time">1m ago</span></div>
    <p class="question__text">What is omitted from the<br>message?</p>
  </article>

  <div class="pager" style="top:636px"><i></i><i></i><i class="on"></i></div>
  <footer class="dock" style="top:658px;padding-top:20px">
    <div class="brand">Civic Viewing Studio</div>
    <div class="dock__url">www.civicviewingstudio.org</div>
  </footer>
</section>

<section class="screen screen--discuss">
  <div class="status"><span class="status__time">11:53</span>
    <svg class="status__icons" width="44" height="10" viewBox="0 0 44 10"><g fill="#fff"><rect x="0" y="6" width="2" height="4"/><rect x="3" y="4" width="2" height="6"/><rect x="6" y="2" width="2" height="8"/><rect x="9" y="0" width="2" height="10"/><rect x="26" y="1" width="16" height="8" rx="2"/></g></svg>
  </div>
  <h1 class="screen__title">TIME TO DISCUSS</h1>

  <!-- row 1 -->
  <div class="app" style="left:14px;top:143px"><div class="app__tile t-teal"><svg viewBox="0 0 34 34"><path d="M5 18l8 8L29 6"/></svg></div>Reality<br>Check</div>
  <div class="app" style="left:93px;top:143px"><div class="app__tile t-green"><svg viewBox="0 0 34 34"><circle cx="20" cy="12" r="7"/><path d="M20 8v8M4 24l6-4h8l-4 4h10l6-5"/></svg></div>Private Gain or<br>Public Good?</div>
  <div class="app" style="left:176px;top:143px"><div class="app__tile t-yellow"><svg viewBox="0 0 34 34"><path d="M17 5a11 10 0 1 1-6 18l-5 4 1-7A11 10 0 0 1 17 5z"/><path d="M14 13a3 3 0 1 1 4 3v2M17 22v.5"/></svg></div>What's<br>Left Out?</div>
  <div class="app" style="left:256px;top:143px"><div class="app__tile t-orange"><svg viewBox="0 0 34 34"><path d="M5 13l6-7h12l6 7-12 15z"/><path d="M5 13h24M11 6l6 22 6-22"/></svg></div>Values<br>Check</div>

  <!-- row 2 -->
  <div class="app" style="left:14px;top:237px"><div class="app__tile t-orange"><svg viewBox="0 0 34 34"><circle cx="17" cy="9" r="4"/><path d="M5 17h24v11H5zM17 17v11M10 14h14"/></svg></div>Read Between<br>the Lines</div>
  <div class="app" style="left:93px;top:237px"><div class="app__tile t-yellow"><svg viewBox="0 0 34 34"><path d="M9 24V15a8 8 0 0 1 16 0v9l2 2H7z"/><path d="M14 28a3 3 0 0 0 6 0M17 5v2"/></svg></div>Stereotype<br>Alert</div>
  <div class="app" style="left:176px;top:237px"><div class="app__tile t-green"><svg viewBox="0 0 34 34"><path d="M6 6h9v4a2 2 0 0 0 4 0V6h9v9h-4a2 2 0 0 0 0 4h4v9H6z"/></svg></div>Solutions<br>too Easy</div>
  <div class="app" style="left:256px;top:237px"><div class="app__tile t-teal"><svg viewBox="0 0 34 34"><circle cx="10" cy="17" r="5"/><circle cx="24" cy="17" r="5"/><path d="M10 22h14"/></svg></div>Record/Save<br>for Later</div>

  <!-- row 3 -->
  <div class="app" style="left:14px;top:335px"><div class="app__tile app__tile--plain"><svg viewBox="0 0 34 34"><path d="M5 10l22-3 2 17-22 3z"/><path d="M9 13l14-2M10 17l14-2M10 21l9-1"/></svg></div>News Media</div>
  <div class="app" style="left:93px;top:335px"><div class="app__tile app__tile--plain"><svg viewBox="0 0 34 34"><circle cx="17" cy="17" r="3"/><circle cx="17" cy="17" r="7"/><circle cx="17" cy="17" r="11"/></svg></div>Websites</div>
  <div class="app" style="left:176px;top:335px"><div class="app__tile app__tile--plain"><svg viewBox="0 0 34 34"><rect x="5" y="7" width="24" height="16"/><path d="M13 28h8M17 23v5"/></svg></div>TV</div>
  <div class="app" style="left:256px;top:335px"><div class="app__tile app__tile--plain"><svg viewBox="0 0 34 34"><rect x="5" y="14" width="24" height="14"/><path d="M5 14l-1-6 23-4 1 6M10 7l3 5M17 6l3 5"/></svg></div>Movies</div>

  <!-- row 4 -->
  <div class="app" style="left:14px;top:429px"><div class="app__tile app__tile--plain"><svg viewBox="0 0 34 34"><rect x="4" y="8" width="26" height="17" rx="2"/><path d="M18 16v10M18 16l5 4"/></svg></div>Apps</div>
  <div class="app" style="left:93px;top:429px"><div class="app__tile app__tile--plain"><svg viewBox="0 0 34 34"><rect x="5" y="11" width="24" height="16" rx="2"/><path d="M8 11l16-5M9 15h9M9 19h9M9 23h9"/><circle cx="24" cy="19" r="3"/></svg></div>Radio</div>
  <div class="app" style="left:176px;top:429px"><div class="app__tile app__tile--plain"><svg viewBox="0 0 34 34"><rect x="6" y="5" width="22" height="24"/><path d="M6 15h22M17 5v10M14 15v14"/></svg></div>Comics</div>
  <div class="app" style="left:256px;top:429px"><div class="app__tile app__tile--plain"><svg viewBox="0 0 34 34"><path d="M17 9c-4-3-9-3-12-2v19c3-1 8-1 12 2 4-3 9-3 12-2V7c-3-1-8-1-12 2zM17 9v19"/></svg></div>Books</div>

  <!-- row 5 -->
  <div class="app" style="left:14px;top:522px"><div class="app__tile app__tile--plain"><svg viewBox="0 0 34 34"><path d="M6 22v-5a11 11 0 0 1 22 0v5"/><rect x="5" y="20" width="5" height="8" rx="2"/><rect x="24" y="20" width="5" height="8" rx="2"/></svg></div>Music</div>
  <div class="app" style="left:93px;top:522px"><div class="app__tile app__tile--plain"><svg viewBox="0 0 34 34"><circle cx="17" cy="17" r="10"/><circle cx="17" cy="7" r="2.5" fill="#fff"/><circle cx="8" cy="22" r="2.5" fill="#fff"/><circle cx="26" cy="22" r="2.5" fill="#fff"/></svg></div>Social Media</div>
  <div class="app" style="left:176px;top:522px"><div class="app__tile app__tile--plain"><svg viewBox="0 0 34 34"><path d="M9 11h16a5 5 0 0 1 5 6l-1 6a3 3 0 0 1-5 1l-3-3h-8l-3 3a3 3 0 0 1-5-1l-1-6a5 5 0 0 1 5-6z"/><path d="M10 15v5M7.5 17.5h5M23 16v.5M26 18v.5"/></svg></div>Video Games</div>
  <div class="app" style="left:256px;top:522px"><div class="app__tile app__tile--plain"><svg viewBox="0 0 34 34"><path d="M17 5v12M11 9a10 10 0 1 0 12 0"/></svg></div>Off</div>

  <div class="pager" style="top:621px"><i></i><i></i><i class="on"></i></div>
  <footer class="dock" style="top:645px;padding-top:36px">
    <div class="brand brand--small"><span class="brand-mark"></span>Civic Viewing Studio</div>
  </footer>
</section>

</body>
</html>
```